Car rental website design for a UAE car rental company

This project is about creating a new website design for a car rental company located in Dubai (United Arab Emirates), I opened the same project a few months ago but I didn't receive a lot of appealing entries so I closed it but this time I am marking the project as guaranteed to avoid such situation again, if you have already provided a design before then please re-submit again on this project so that it is considered while reviewing all the designs

A few important things:

1- We need a simple non-complex design
2- The final deliverable would be 2 screens (PSD, JPEG ... etc), the first screen is for the home page and the second screen is for an internal page
3- The home page must have a section that end users can use to rent a car online directly from the home page instead of going into some inner pages
4- The current website is very old and not very appealing so avoid creating a similar design (www.crestvane-autos.example)
5- The name is Crestvane but the company rents normal cars (no Limousin cars will be rented) so avoid adding any fancy cars in the images/graphics used in the design, just normal end users cars
6- The expected pages would be: home, About us, Our team, Strategy, Contact us and links to social media pages
7- The attachments include the company's logo and some screens from other car rental companies that provide online rentals/payments

If you have any questions please feel free to ask and please note that we will need the designs urgently

Thanks

Target Market(s)

Dubai - United Arab Emirates

Industry/Entity Type

It Company

Number of Pages Required

2 page

Font styles to use
Sans Serif

Requirements
Must have
• Check the project details
Nice to have
Should not have

```html
<!DOCTYPE html>
<html lang="en">
<head>
<meta charset="utf-8">
<title>Crestvane Rent A Car</title>
<link rel="stylesheet" href="https://fonts.googleapis.com/css2?family=Roboto+Slab:wght@300;400&family=Roboto+Condensed:wght@400&family=Roboto:wght@400;500&display=swap">
<style>
:root{
  --crimson:#a3113f;
  --grey:#8c918e;
  --grey-dark:#5d615f;
  --ink:#2e2e2e;
  --light:#f3f3f3;
  --white:#ffffff;
  --field:#f6f6f6;
}
*{box-sizing:border-box;margin:0;padding:0}
html,body{width:920px;height:1200px;overflow:hidden;background:var(--white)}
body{position:relative;font-family:'Roboto Slab',serif;color:var(--ink);font-weight:300}
.abs{position:absolute}

/* header */
.site-header{position:absolute;left:0;top:0;width:920px;height:80px;background:linear-gradient(#fbfbfb,#ececec);border-bottom:1px solid var(--crimson);border-top:2px solid #d0d0d0}
.brand{position:absolute;left:62px;top:10px;display:flex;align-items:center;gap:8px}
.brand-mark{width:56px;height:56px;border:2px solid var(--crimson);background:var(--white)}
.brand-name{font-size:28px;font-weight:400;color:var(--grey)}
.brand-sub{display:block;font-size:13px;color:var(--crimson);letter-spacing:2px;margin-top:-4px;padding-left:26px}
.social{position:absolute;display:flex;gap:8px}
.social span{width:18px;height:18px;border-radius:50%;background:#3b5fa0;display:block}
.social span:nth-child(2){background:#3fa1dc}
.social span:nth-child(3){background:#1f6fb0}
.social span:nth-child(4){background:#d3412f}
.header-social{left:464px;top:14px}
.phone{position:absolute;left:648px;top:8px;display:flex;align-items:center;gap:6px;font-size:15px;color:var(--crimson);font-weight:400}
.main-nav{position:absolute;top:54px;left:462px;display:flex;gap:19px;font-size:13px;color:var(--grey)}
.main-nav .active{color:var(--crimson)}

/* hero */
.hero{position:absolute;left:0;top:81px;width:920px;height:335px;background:linear-gradient(100deg,#3a3d42 0%,#a9acb0 28%,#e7e8ea 55%,#cfd0d2 80%,#7c7f84 100%);border-bottom:3px solid var(--crimson)}
.hero-headline{position:absolute;left:67px;top:16px;font-family:'Roboto Condensed',sans-serif;font-size:24px;line-height:29px;color:var(--white)}
.booking{position:absolute;left:537px;top:82px;width:323px;height:334px;background:var(--crimson);padding:0 4px 4px}
.booking-tabs{display:flex;height:34px;align-items:flex-end;font-size:12px;color:var(--white)}
.booking-tabs .tab-active{background:var(--grey);padding:6px 8px;font-size:13px;font-weight:400}
.booking-tabs .tab{padding:8px 10px}
.booking-body{position:relative;height:296px;background:rgba(255,255,255,.88);font-size:11px}
.step{position:absolute;left:4px;width:20px;height:20px;border:1px solid var(--crimson);background:var(--white);text-align:center;line-height:18px;font-size:12px}
.label{position:absolute;left:41px;font-size:11px;font-weight:400;color:var(--ink)}
.link{position:absolute;left:41px;color:var(--crimson);text-decoration:underline;font-size:11px;font-weight:400}
.field{position:absolute;height:21px;border:1px solid #999;background:var(--field);font-size:9.5px;padding:4px 5px;font-weight:400}
.check{position:absolute;display:flex;align-items:center;gap:4px;font-size:10.5px;font-weight:400}
.check i{width:8px;height:8px;border:1px solid #555;display:block}
.help{width:14px;height:14px;border-radius:50%;background:var(--grey);color:var(--white);font-size:8px;text-align:center;line-height:14px;font-style:normal}
.quote-btn{position:absolute;right:10px;bottom:0;background:var(--crimson);color:var(--white);font-size:13px;font-weight:400;padding:8px 18px}

/* features */
.features{position:absolute;left:0;top:419px;width:920px;height:208px;background:var(--light);border-bottom:1px solid #ddd}
.feature{position:absolute;top:25px;width:190px;text-align:center;transform:translateX(-50%)}
.feature-icon{width:72px;height:72px;border:2px solid var(--grey);border-radius:50%;margin:0 auto 12px;display:flex;align-items:center;justify-content:center;background:var(--white)}
.feature-icon.is-active{border-color:var(--crimson)}
.feature h3{font-size:12px;font-weight:400;line-height:16px;height:36px}
.feature p{font-family:'Roboto',sans-serif;font-size:11.5px;line-height:15.5px;color:#444}
.slider-arrow{position:absolute;top:510px;color:#fff;font-size:18px}

/* sections */
.section-title{position:absolute;left:0;width:920px;text-align:center;font-size:15px;color:var(--grey)}
.section-title em{font-style:normal;color:var(--crimson)}
.dash{position:absolute;height:0;border-top:1px dashed var(--grey)}
.deal{position:absolute;top:692px;width:166px}
.deal-photo{height:88px;border-radius:40% 40% 10% 10%;}
.deal-photo.silver{background:radial-gradient(ellipse at center,#c7c9cb 0%,#9a9c9f 55%,transparent 72%)}
.deal-photo.red{background:radial-gradient(ellipse at center,#d8262b 0%,#a31318 55%,transparent 72%)}
.deal-price{background:var(--grey);color:var(--white);font-size:13px;font-weight:400;text-align:center;padding:8px 0}
.divider{position:absolute;left:64px;width:792px;height:10px;background:radial-gradient(ellipse at top,rgba(0,0,0,.12),transparent 70%)}
.copy{position:absolute;left:80px;width:760px;text-align:center;font-size:11.5px;line-height:17px;font-weight:400;color:#333}
.read-more{position:absolute;top:966px;left:0;width:920px;text-align:center;font-size:12px;font-weight:400}

/* footer */
.site-footer{position:absolute;left:0;top:1156px;width:920px;height:44px;background:var(--crimson);color:var(--white)}
.footer-nav{position:absolute;left:62px;top:15px;display:flex;gap:14px;font-size:11.5px;font-weight:400}
.footer-social{left:511px;top:13px}
.footer-social span{border:1px solid #fff}
.copyright{position:absolute;right:60px;top:15px;font-family:'Roboto',sans-serif;font-size:11px;font-weight:500}
</style>
</head>
<body>

<header class="site-header">
  <div class="brand">
    <div class="brand-mark"></div>
    <div><span class="brand-name">Crestvane</span><span class="brand-sub">Rent A Car</span></div>
  </div>
  <div class="social header-social"><span></span><span></span><span></span><span></span></div>
  <div class="phone">
    <svg width="28" height="30" viewBox="0 0 28 30"><path d="M4 16a10 10 0 0 1 20 0" fill="none" stroke="#888" stroke-width="3"/><rect x="2" y="15" width="6" height="9" rx="2" fill="#a3113f"/><rect x="20" y="15" width="6" height="9" rx="2" fill="#a3113f"/><path d="M23 24q0 4-6 4" fill="none" stroke="#888" stroke-width="2"/></svg>
    Call us at +971 4 555 0199
  </div>
  <nav class="main-nav"><span class="active">HOME</span><span>ABOUT US</span><span>OUR TEAM</span><span>STRATEGY</span><span>CONTACT US</span></nav>
</header>

<section class="hero" role="img" aria-label="Silver saloon car photographed in profile on a grey studio background">
  <h1 class="hero-headline" style="font-weight:400">Experience An Extra<br>Mile of comfort,<br>pleasure and leisure<br>From the best</h1>
</section>

<form class="booking" aria-label="Book a car">
  <div class="booking-tabs"><span class="tab-active">Book A Car</span><span class="tab">View / Modify / Cancel A Reservation</span></div>
  <div class="booking-body">
    <span class="step" style="top:9px">1</span>
    <span class="label" style="top:12px">Pick-up Location &nbsp;(City, State or Airport Code</span>
    <span class="link" style="top:29px">Previous Searches</span>
    <div class="field" style="left:41px;top:45px;width:260px">Dubai Airport - Terminal 3</div>
    <span class="link" style="top:75px">Help me find a rental location</span>
    <div class="check" style="left:41px;top:94px"><i></i>Return car to a different Crestvane Location <b class="help">?</b></div>
    <span class="step" style="top:119px">2</span>
    <span class="label" style="top:122px">Pick-up Date &amp; Time</span>
    <div class="field" style="left:41px;top:139px;width:128px">26/03/2015</div>
    <div class="field" style="left:173px;top:139px;width:128px">16:00</div>
    <span class="label" style="top:171px">Return Date &amp; Time</span>
    <div class="field" style="left:41px;top:188px;width:128px">26/03/2015</div>
    <div class="field" style="left:173px;top:188px;width:128px">16:00</div>
    <span class="label" style="top:220px">Hire Car Type</span>
    <div class="field" style="left:41px;top:237px;width:128px">Automatic</div>
    <div class="check" style="left:175px;top:240px"><i></i>Apply a discount Code <b class="help">?</b></div>
    <span class="quote-btn">Get A Quote</span>
  </div>
</form>

<section class="features">
  <div class="feature" style="left:154px">
    <div class="feature-icon is-active"><svg width="44" height="34" viewBox="0 0 44 34"><rect x="2" y="10" width="26" height="10" rx="3" fill="#a3113f"/><rect x="7" y="3" width="16" height="9" rx="3" fill="#a3113f"/><rect x="14" y="21" width="28" height="10" rx="3" fill="#a3113f"/><rect x="19" y="14" width="18" height="9" rx="3" fill="#a3113f"/></svg></div>
    <h3>Wide Range Of Vehicles For City Driving or SUV's For Trips</h3>
    <p>Lorem ipsum dolor sit aonsectetuer adipiscing elied diam nonummy</p>
  </div>
  <div class="feature" style="left:370px">
    <div class="feature-icon"><svg width="34" height="34" viewBox="0 0 34 34"><path d="M18 3h12v12L15 30 3 18z" fill="#8c918e"/><circle cx="24" cy="9" r="2.5" fill="#fff"/></svg></div>
    <h3>Special 10% Discount For New Customers On The First Rent</h3>
    <p>Lorem ipsum dolor sit aonsectetuer adipiscing elied diam nonummy</p>
  </div>
  <div class="feature" style="left:575px">
    <div class="feature-icon"><svg width="34" height="38" viewBox="0 0 34 38"><circle cx="11" cy="7" r="5" fill="#5d615f"/><rect x="14" y="5" width="16" height="4" fill="#5d615f"/><rect x="4" y="22" width="26" height="10" rx="3" fill="#5d615f"/><rect x="8" y="15" width="18" height="9" rx="3" fill="#5d615f"/></svg></div>
    <h3>Long Term Car<br>Rentals</h3>
    <p>Lorem ipsum dolor sit aonsectetuer adipiscing elied diam nonummy</p>
  </div>
  <div class="feature" style="left:780px">
    <div class="feature-icon"><svg width="34" height="34" viewBox="0 0 34 34"><path d="M12 6 4 13l8 7v-5h8a6 6 0 0 1 0 12h-4v4h4a10 10 0 0 0 0-20h-8z" fill="#5d615f"/></svg></div>
    <h3>Buyback Option After<br>Lease Term</h3>
    <p>Lorem ipsum dolor sit aonsectetuer adipiscing elied diam nonummy</p>
  </div>
</section>
<span class="slider-arrow" style="left:32px">&#8249;</span>
<span class="slider-arrow" style="left:878px">&#8250;</span>

<h2 class="section-title" style="top:650px;font-weight:300">Grab the <em>Best Deal Today</em></h2>
<div class="dash" style="left:328px;top:674px;width:264px"></div>
<div class="deal" style="left:76px"><div class="deal-photo silver" role="img" aria-label="Silver family saloon"></div><div class="deal-price">From Only AED 1100 p/m</div></div>
<div class="deal" style="left:280px"><div class="deal-photo red" role="img" aria-label="Red family saloon"></div><div class="deal-price">From Only AED 1100 p/m</div></div>
<div class="deal" style="left:480px"><div class="deal-photo silver" role="img" aria-label="Silver family saloon"></div><div class="deal-price">From Only AED 1100 p/m</div></div>
<div class="deal" style="left:684px"><div class="deal-photo red" role="img" aria-label="Red family saloon"></div><div class="deal-price">From Only AED 1100 p/m</div></div>

<div class="divider" style="top:836px"></div>

<h2 class="section-title" style="top:866px;font-weight:300">Welcome to Crestvane <em>Rent A Car</em></h2>
<div class="dash" style="left:280px;top:888px;width:360px"></div>
<p class="copy" style="top:894px">As Dubai is expected to welcome millions of tourists and visitors, car rental industry is believed to escalate more rapidly in the region. Over the past five years, demands for car rentals in Dubai has been augmenting at a healthy pace and is currently registering a growth rate of 20 to 25 percent per year. The swift economic growth and the number. Crestvane was established to bring comfort and pleasure to all its clients. First rate service plus highly maintained and top...</p>
<p class="read-more">Read More</p>

<div class="divider" style="top:1006px"></div>

<h2 class="section-title" style="top:1036px;font-weight:300">Our <em>Mission</em></h2>
<div class="dash" style="left:280px;top:1058px;width:360px"></div>
<p class="copy" style="top:1071px;left:70px;width:780px">To be one of the leading auto leasing company in the fast growing economy and tourism industry of the emirate of Dubai &amp; play alongside with the major car rental companies in the globe.<br><span style="display:block;margin-top:3px">Crestvane vows to deliver comfort, luxury &amp; satisfaction to all our clients by providing them professional, hassle-free and first class service.</span></p>

<footer class="site-footer">
  <nav class="footer-nav"><span>HOME</span><span>ABOUT US</span><span>OUR TEAM</span><span>STRATEGY</span><span>CONTACT US</span></nav>
  <div class="social footer-social"><span></span><span></span><span></span><span></span></div>
  <p class="copyright">© 2015 Crestvane. All Rights Reserved</p>
</footer>

</body>
</html>
```